SkyvornQ Business Cards and Stationary Design

Need a design for our business cards and stationary. I want to carry on the theme of the logo. I want the business cards to have a design on the back. I would like the business cards and the stationary to carry the same theme, design scheme, and branding

Target Market(s)

Airlines and Maintenance Facilities

Industry/Entity Type

Aviation

Contact Information for Business Card

Name
Position Title
Address: 4827 Trellis Hollow Road, Fort Pierce, Florida, 34951
Office Number
Mobile Number
Email
Website

Font styles to use
Serif
Sans Serif

Colors

Designer to choose colors to be used in the design.

```html
<!DOCTYPE html>
<html lang="en">
<head>
<meta charset="utf-8">
<title>SkyvornQ Business Card</title>
<link rel="stylesheet" href="https://fonts.googleapis.com/css2?family=Open+Sans:wght@400;600;700&display=swap">
<style>
  :root{
    --navy:#0d2a55;
    --blue:#1479c4;
    --blue-light:#2d9be0;
    --blue-deep:#0a4f93;
    --ink:#3a3a3a;
    --rule:#c9c9c9;
    --paper:#ffffff;
    --bg:#e9ecef;
  }
  html,body{margin:0;padding:0;overflow:hidden}
  body{
    width:1200px;height:872px;background:var(--bg);
    font-family:"Open Sans",Arial,sans-serif;
    position:relative;
  }
  .card{
    position:absolute;width:560px;height:320px;
    box-shadow:0 6px 18px rgba(0,0,0,.18);
    overflow:hidden;
  }
  /* back side */
  .card-back{
    left:30px;top:120px;
    background:radial-gradient(ellipse at 50% 45%,var(--blue-light) 0%,var(--blue) 45%,var(--blue-deep) 100%);
    color:#fff;
  }
  .card-back .brand{
    position:absolute;left:0;right:0;top:105px;
    display:flex;align-items:center;justify-content:center;gap:14px;
  }
  .card-back .brand-dot{width:46px;height:46px;border-radius:50%;border:4px solid #fff;box-sizing:border-box}
  .card-back .brand-name{font-weight:700;font-size:40px;letter-spacing:3px;color:#fff}
  .card-back .web{
    position:absolute;left:0;right:0;bottom:58px;text-align:center;
    font-size:17px;letter-spacing:4px;
  }
  /* front side */
  .card-front{
    left:610px;top:432px;background:var(--paper);
  }
  .logo-block{
    position:absolute;left:34px;top:110px;
    display:flex;align-items:center;gap:12px;
  }
  .logo-dot{width:38px;height:38px;border-radius:50%;border:4px solid var(--blue);box-sizing:border-box}
  .logo-name{font-weight:700;font-size:34px;letter-spacing:4px;color:var(--navy)}
  .divider{position:absolute;left:330px;top:50px;width:1px;height:160px;background:var(--rule)}
  .contact{position:absolute;left:350px;top:44px;color:var(--ink)}
  .contact .name{font-weight:700;font-size:19px;color:var(--navy);text-transform:uppercase;letter-spacing:.2px}
  .contact .title{font-size:17px;color:#555;text-transform:uppercase;margin-top:2px;margin-bottom:12px}
  .contact ul{list-style:none;margin:0;padding:0}
  .contact li{display:flex;align-items:center;gap:7px;font-size:14px;line-height:22px}
  .contact svg{width:13px;height:13px;flex:none}
  .footer-rule{position:absolute;left:0;right:0;bottom:46px;height:1.5px;background:var(--blue-deep)}
  .footer-band{
    position:absolute;left:0;right:0;bottom:0;height:38px;
    background:linear-gradient(180deg,var(--blue-light),var(--blue-deep));
    color:#fff;font-size:14px;display:flex;align-items:center;justify-content:center;gap:8px;
  }
  .footer-band svg{width:13px;height:13px}
</style>
</head>
<body>

<section class="card card-back">
  <div class="brand">
    <span class="brand-dot"></span>
    <span class="brand-name">SkyvornQ</span>
  </div>
  <div class="web">www.skyvornq.com</div>
</section>

<section class="card card-front">
  <div class="logo-block">
    <span class="logo-dot"></span>
    <span class="logo-name">SKYVORNQ</span>
  </div>
  <div class="divider"></div>
  <div class="contact">
    <div class="name">Marcus Delloway</div>
    <div class="title">President</div>
    <ul>
      <li><svg viewBox="0 0 16 16"><circle cx="8" cy="8" r="7" fill="none" stroke="#0d2a55" stroke-width="1.5"/><path d="M5.5 4.5l1.5 0 .6 1.8-1 .8a5 5 0 0 0 2.3 2.3l.8-1 1.8.6 0 1.5c-3.5.3-6.3-2.5-6-6z" fill="#0d2a55"/></svg>014-275-3896</li>
      <li><svg viewBox="0 0 16 16"><circle cx="8" cy="8" r="7" fill="none" stroke="#0d2a55" stroke-width="1.5"/><rect x="5.8" y="4" width="4.4" height="8" rx=".8" fill="none" stroke="#0d2a55" stroke-width="1.2"/></svg>014-275-3896</li>
      <li><svg viewBox="0 0 16 16"><circle cx="8" cy="8" r="7" fill="none" stroke="#0d2a55" stroke-width="1.5"/><rect x="4.5" y="5.5" width="7" height="5" fill="none" stroke="#0d2a55" stroke-width="1.2"/><path d="M4.5 5.5l3.5 3 3.5-3" fill="none" stroke="#0d2a55" stroke-width="1.2"/></svg>info@skyvornq.com</li>
      <li><svg viewBox="0 0 16 16"><circle cx="8" cy="8" r="7" fill="none" stroke="#0d2a55" stroke-width="1.5"/><ellipse cx="8" cy="8" rx="3" ry="7" fill="none" stroke="#0d2a55" stroke-width="1.1"/><path d="M1 8h14" stroke="#0d2a55" stroke-width="1.1"/></svg>www.skyvornq.com</li>
    </ul>
  </div>
  <div class="footer-rule"></div>
  <div class="footer-band">
    <svg viewBox="0 0 16 16"><circle cx="8" cy="8" r="7" fill="none" stroke="#fff" stroke-width="1.5"/><path d="M8 12.5s-3-3.2-3-5.3a3 3 0 0 1 6 0c0 2.1-3 5.3-3 5.3z" fill="#fff"/><circle cx="8" cy="7.2" r="1" fill="#1479c4"/></svg>
    4827 Trellis Hollow Road, Fort Pierce, Florida, 34951
  </div>
</section>

</body>
</html>
```